Property management company looking for modern card design

We at Blue Heron Partners provides property management services for its residential and commercial properties, with expertise in all categories of multifamily, industrial and office projects throughout California.

We need a business card design that is professional and modern designed business card. In our field, clients get hundreds of business cards, we would like our card to stand out.

Please avoid small print.

Target Market(s)

Professionals and high end clients

Industry/Entity Type

Financial Planning

Contact Information for Business Card

Company Name: Blue Heron Partners, Name, email, license #, phone number, website blueheronpartners.com

Font styles to use
Sans Serif

Requirements
Must have
• The card design needs to be adaptable because there is a possibly we will be expanding into different sectors other than real estate. The card design should be focused on financial planning and asset management.
Nice to have
• Modern and simple business card. Eye catching. Non-standard size/shaped cards would be great.
• blueheronpartners.com
Should not have
• Too many bright color or any pictures or shapes of real estate stuff.

```html
<!DOCTYPE html>
<html lang="en">
<head>
<meta charset="UTF-8">
<title>Blue Heron Partners – Business Card</title>
<link rel="stylesheet" href="https://fonts.googleapis.com/css2?family=Montserrat:wght@400;500;600;700&family=Open+Sans:wght@600;700&display=swap">
<style>
  :root {
    --bg: #e9e7e4;
    --card: #ffffff;
    --brand-red: #cf3535;
    --ink: #2b2b2b;
    --rule: #9a9a9a;
    --shadow: rgba(0, 0, 0, 0.18);
  }
  * { box-sizing: border-box; margin: 0; padding: 0; }
  html, body {
    width: 1200px;
    height: 1000px;
    overflow: hidden;
    background: var(--bg);
    font-family: "Montserrat", sans-serif;
    color: var(--ink);
  }
  .canvas { position: relative; width: 1200px; height: 1000px; }

  .card {
    position: absolute;
    left: 288px;
    width: 625px;
    height: 356px;
    background: var(--card);
    border-radius: 24px;
    box-shadow: 0 6px 14px var(--shadow);
  }
  .card--front { top: 141px; }
  .card--back { top: 533px; }

  /* Front */
  .wordmark {
    position: absolute;
    left: 0; right: 0;
    top: 150px;
    display: flex;
    align-items: center;
    justify-content: center;
    gap: 16px;
  }
  .wordmark__dot {
    width: 34px; height: 34px;
    border-radius: 50%;
    background: var(--brand-red);
    flex: none;
  }
  .wordmark__name {
    font-size: 38px;
    font-weight: 400;
    letter-spacing: 1px;
    color: var(--ink);
    white-space: nowrap;
  }

  /* Back */
  .brand-disc {
    position: absolute;
    left: 86px; top: 88px;
    width: 180px; height: 180px;
    border-radius: 50%;
    background: var(--brand-red);
    display: flex;
    align-items: center;
    justify-content: center;
    text-align: center;
  }
  .brand-disc__name {
    color: #fff;
    font-size: 19px;
    font-weight: 500;
    line-height: 1.3;
    letter-spacing: 1px;
  }
  .divider {
    position: absolute;
    left: 297px; top: 100px;
    width: 1px; height: 158px;
    background: linear-gradient(to bottom, rgba(0,0,0,0), var(--rule) 20%, var(--rule) 80%, rgba(0,0,0,0));
  }
  .contact {
    position: absolute;
    left: 327px; top: 97px;
  }
  .contact__name {
    font-family: "Open Sans", sans-serif;
    font-weight: 700;
    font-size: 22px;
    color: var(--brand-red);
    line-height: 1.1;
  }
  .contact__title { font-size: 14px; margin-top: 2px; }
  .contact__license { font-size: 15px; margin-top: 18px; }
  .contact__license-label { color: var(--brand-red); }
  .contact__list { list-style: none; margin-top: 16px; }
  .contact__item {
    display: flex; align-items: center; gap: 8px;
    font-size: 14.5px; height: 23px;
  }
  .contact__icon { width: 13px; height: 13px; flex: none; }
</style>
</head>
<body>
<div class="canvas">

  <section class="card card--front" aria-label="Card front">
    <div class="wordmark">
      <span class="wordmark__dot"></span>
      <span class="wordmark__name">BLUE HERON PARTNERS</span>
    </div>
  </section>

  <section class="card card--back" aria-label="Card back">
    <div class="brand-disc">
      <span class="brand-disc__name">BLUE HERON<br>PARTNERS</span>
    </div>
    <div class="divider"></div>
    <div class="contact">
      <div class="contact__name">Daniel Reyes</div>
      <div class="contact__title">President</div>
      <div class="contact__license"><span class="contact__license-label">License:</span> #7318406</div>
      <ul class="contact__list">
        <li class="contact__item">
          <svg class="contact__icon" viewBox="0 0 16 16" aria-hidden="true">
            <path fill="var(--brand-red)" d="M3.6 1.5l2.3 2.6-1.3 1.6c.9 2 2.3 3.4 4.3 4.3l1.6-1.3 2.6 2.3-1.5 2.3C6.9 13.6 2.4 9.1 1.3 3z"/>
          </svg>
          <span>555-0142-7731</span>
        </li>
        <li class="contact__item">
          <svg class="contact__icon" viewBox="0 0 16 16" aria-hidden="true">
            <rect x="1" y="3" width="14" height="10" rx="1" fill="var(--brand-red)"/>
            <path d="M1.5 3.8L8 9l6.5-5.2" fill="none" stroke="#fff" stroke-width="1.3"/>
          </svg>
          <span>info@blueheronpartners.com</span>
        </li>
        <li class="contact__item">
          <svg class="contact__icon" viewBox="0 0 16 16" aria-hidden="true">
            <circle cx="8" cy="8" r="7" fill="var(--brand-red)"/>
            <g fill="none" stroke="#fff" stroke-width="1">
              <ellipse cx="8" cy="8" rx="3" ry="7"/>
              <path d="M1 8h14M2.2 4.5h11.6M2.2 11.5h11.6"/>
            </g>
          </svg>
          <span>www.blueheronpartners.com</span>
        </li>
      </ul>
    </div>
  </section>

</div>
</body>
</html>
```